Clearvale glass & hardware manufacturer

Need a SEO friendly, modern & professional looking website. We are selling all kinds of glass & accessories ( Glass/ Mirror/ splash back/ pool fence/ balustrade/ hardware...we are specialised on some special glass, like curve glass,tinted glass thermal & accoustic glass...) It should has simple & crisp feeling like a glass. It must be fully functional with product display and online ordering. Please see attached confirmed logo design(Blue & white). Make sure the theme color match its feel.

Target Market(s)

Architect and designer, Builder, & Developer

Industry/Entity Type

Manufacturer

Coding

Coded - Design and coding required

Font styles to use
Serif
Sans Serif

Colors

Designer to choose colors to be used in the design.

Requirements
Must have
• Glass & hardware theme and our logo
• Here are some competitor's website for reference. (Borrow ideas but not copy : )
• 1.https://www.tarvino.com.au/about
• 2.http://www.plumeretail.com.au/
• 3.http://www.kwd.com.au/
• 4.http://www.brackenhillfittings.com.au/
Nice to have
• Some transparent or semi transparent effects to make the website like a glass
Should not have
• No limitation for your imagination

```html
<!DOCTYPE html>
<html lang="en">
<head>
<meta charset="utf-8">
<title>Clearvale Glass &amp; Hardware</title>
<link rel="stylesheet" href="https://fonts.googleapis.com/css2?family=Montserrat:wght@400;500;600&display=swap">
<style>
:root{
  --brand:#1a5fb0;
  --brand-dark:#1458a8;
  --accent:#2b8fd6;
  --band:rgba(22,88,168,.88);
  --text:#333;
  --muted:#555;
  --white:#fff;
  --line:#d9e2ec;
}
*{margin:0;padding:0;box-sizing:border-box}
html,body{width:670px;height:1200px;overflow:hidden}
body{position:relative;background:#fff;font-family:Arial,Helvetica,sans-serif;color:var(--text)}
.site-header{position:absolute;top:0;left:0;width:670px;height:52px;background:#fff}
.brand{position:absolute;left:49px;top:11px;display:flex;align-items:center;gap:7px;font-family:'Montserrat',sans-serif;font-weight:600;font-size:14px;color:var(--brand);letter-spacing:.5px}
.brand-mark{width:24px;height:24px;background:var(--brand);border-radius:50%}
.brand small{display:block;font-size:7px;letter-spacing:1.6px;font-weight:600}
.main-nav{position:absolute;top:22px;right:49px;display:flex;gap:21px;font-family:'Montserrat',sans-serif;font-size:7.5px;font-weight:500;color:#555}
.main-nav .active{color:var(--brand)}
.hero{position:absolute;top:52px;left:0;width:670px;height:282px;background:linear-gradient(180deg,#6d93c2 0%,#a9c3e0 45%,#d8e4f1 75%,#9fb7d4 100%)}
.hero-box{position:absolute;left:162px;top:119px;width:337px;height:94px;background:rgba(72,128,196,.55);text-align:center;color:#fff}
.hero-box h1{font-family:'Montserrat',sans-serif;font-weight:500;font-size:18.5px;margin-top:24px;white-space:nowrap}
.hero-box p{font-family:'Montserrat',sans-serif;font-size:11px;margin-top:8px;letter-spacing:.3px;white-space:nowrap}
.slider-dots{position:absolute;top:265px;left:320px;display:flex;gap:2px}
.slider-dots span{width:9px;height:9px;border:1.5px solid #123;border-radius:50%}
.slider-dots span.on{border-color:#2a6ab8}
.content{position:absolute;top:334px;left:0;width:670px;height:735px;background:linear-gradient(180deg,#e6ebf0 0%,#f4f6f8 40%,#eef2f5 100%)}
.section-title{position:absolute;width:670px;text-align:center;font-family:'Montserrat',sans-serif;font-weight:500;font-size:15px;color:var(--brand)}
.section-text{position:absolute;width:670px;text-align:center;font-size:7px;color:var(--muted);line-height:15.5px}
.product{position:absolute;width:186px;height:154px}
.product .photo{height:126px}
.product .label{height:28px;background:var(--band);color:#fff;font-family:'Montserrat',sans-serif;font-weight:500;font-size:10px;display:flex;align-items:center;justify-content:center}
.btn{position:absolute;left:263px;width:144px;height:29px;border-radius:15px;font-family:'Montserrat',sans-serif;font-weight:500;font-size:8.5px;display:flex;align-items:center;justify-content:center}
.btn-solid{background:var(--accent);color:#fff}
.btn-outline{border:1px solid var(--accent);color:var(--brand);background:transparent}
.divider{position:absolute;top:465px;left:132px;width:406px;height:1px;background:var(--line)}
.partner{position:absolute;top:638px;width:102px;height:58px;background:#fff;border:2px solid #e2e6ea;box-shadow:0 0 0 1px #cfd5db;display:flex;align-items:center;justify-content:center;font-family:'Montserrat',sans-serif;font-size:11px;font-weight:500;color:#777}
.arrow{position:absolute;top:648px}
.site-footer{position:absolute;top:1069px;left:0;width:670px;height:131px;background:var(--brand-dark);color:#fff}
.social{position:absolute;top:18px;left:218px;display:flex;gap:6px}
.social span{width:34px;height:34px;border:1px solid rgba(255,255,255,.55);border-radius:50%;display:flex;align-items:center;justify-content:center;font-family:'Montserrat',sans-serif;font-size:6.5px;font-weight:500;color:#fff}
.footer-rule{position:absolute;top:60px;left:132px;width:406px;height:1px;background:rgba(255,255,255,.2)}
.footer-nav{position:absolute;top:73px;width:670px;display:flex;justify-content:center;gap:14px;font-family:'Montserrat',sans-serif;font-size:7.5px;font-weight:500}
.copyright{position:absolute;top:96px;width:670px;text-align:center;font-family:'Montserrat',sans-serif;font-size:7.5px;font-weight:500}
</style>
</head>
<body>
<header class="site-header">
  <div class="brand"><span class="brand-mark"></span><div>CLEARVALE<small>GLASS &amp; HARDWARE</small></div></div>
  <nav class="main-nav"><span class="active">HOME</span><span>ABOUT US</span><span>PRODUCTS</span><span>SERVICES</span><span>BLOG</span><span>CONTACT</span></nav>
</header>

<section class="hero" role="img" aria-label="Bright airport corridor with curved glass balustrade">
  <div class="hero-box"><h1>CLEARVALE GLASS &amp; HARDWARES</h1><p>SED UT PERSPICIATIS UNDE OMNIS ISTE NATUS</p></div>
  <div class="slider-dots"><span></span><span class="on"></span><span></span></div>
</section>

<main class="content">
  <h2 class="section-title" style="top:19px">OUR PRODUCTS</h2>
  <p class="section-text" style="top:41px">Sed ut perspiciatis unde omnis iste natus error sit voluptatem accusantium doloremque laudantium</p>

  <div class="product" style="left:48px;top:69px"><div class="photo" role="img" aria-label="Office with glass partition walls" style="background:linear-gradient(180deg,#e9edf0,#c9d2d8)"></div><div class="label">GLASS</div></div>
  <div class="product" style="left:243px;top:69px"><div class="photo" role="img" aria-label="Kitchen with glass splash back" style="background:linear-gradient(180deg,#cfd3d2,#8d7c6a)"></div><div class="label">SPLASH BACK</div></div>
  <div class="product" style="left:437px;top:69px"><div class="photo" role="img" aria-label="Pool with frameless glass fence by the sea" style="background:linear-gradient(180deg,#b7c3e0,#7fb3d6 50%,#3cb3d8)"></div><div class="label">POOL FENCE</div></div>
  <div class="product" style="left:48px;top:235px"><div class="photo" role="img" aria-label="Gloved hands lifting glass with suction cups" style="background:linear-gradient(180deg,#c8d3b8,#e4e8e2)"></div><div class="label">SPECIAL GLASS</div></div>
  <div class="product" style="left:243px;top:235px"><div class="photo" role="img" aria-label="Curved glass wall along a bright corridor" style="background:linear-gradient(180deg,#8fb0d2,#d6e2ee)"></div><div class="label">CURVE GLASS</div></div>
  <div class="product" style="left:437px;top:235px"><div class="photo" role="img" aria-label="Curved tinted glass facade against blue sky" style="background:linear-gradient(135deg,#2e5fa8,#5d86c4 60%,#c5d3e4)"></div><div class="label">TINTED GLASS</div></div>

  <a class="btn btn-solid" style="top:418px">VIEW MORE PRODUCTS</a>
  <div class="divider"></div>

  <h2 class="section-title" style="top:488px">ABOUT OUR COMPANY</h2>
  <p class="section-text" style="top:516px">Sed ut perspiciatis unde omnis iste natus error sit voluptatem accusantium doloremque laudantium, totam rem aperiam, eaque ipsa<br>quae ab illo inventore veritatis et quasi architecto beatae vitae dicta sunt explicabo. Nemo enim ipsam voluptatem quia voluptas sit aut<br>fugit, sed quia consequuntur magni dolores eos qui ratione voluptatem sequi nesciunt.</p>
  <a class="btn btn-outline" style="top:579px">CLICK HERE FOR MORE INFO</a>

  <svg class="arrow" style="left:26px" width="10" height="36" viewBox="0 0 10 36"><path d="M9 1 1 18l8 17" fill="none" stroke="#c4ccd4" stroke-width="1"/></svg>
  <div class="partner" style="left:57px">Norvik</div>
  <div class="partner" style="left:171px">Tessa</div>
  <div class="partner" style="left:285px">Lumora</div>
  <div class="partner" style="left:400px">Kestrel Works</div>
  <div class="partner" style="left:513px">Aldren</div>
  <svg class="arrow" style="left:634px" width="10" height="36" viewBox="0 0 10 36"><path d="M1 1l8 17-8 17" fill="none" stroke="#c4ccd4" stroke-width="1"/></svg>
</main>

<footer class="site-footer">
  <div class="social">
    <span>Folio</span><span>Chirpa</span><span>Plexa</span><span>Linko</span><span>Snapa</span>
    <span aria-label="Email"><svg width="11" height="8" viewBox="0 0 11 8"><rect x=".5" y=".5" width="10" height="7" fill="none" stroke="#fff"/><path d="M.5.5l5 4 5-4" fill="none" stroke="#fff"/></svg></span>
  </div>
  <div class="footer-rule"></div>
  <nav class="footer-nav"><span>HOME</span><span>|</span><span>ABOUT US</span><span>|</span><span>PRODUCTS</span><span>|</span><span>SERVICES</span><span>|</span><span>BLOG</span><span>|</span><span>CONTACT</span></nav>
  <p class="copyright">© Copyrights 2018 Clearvale glass &amp; hardwares.All Rights Reserved.</p>
</footer>
</body>
</html>
```